Brightway Haul & Upkeep Services, are a company that offers a 'one stop shop' pre-move clean up a

I have already selected a logo which I would like on the front of the business cards along with phone numbers, web address and email which are:
0487650392
www.brightwayhaul.com.au
brightwayhaulandupkeep@mailbox.example

On the back of the card I would like to list some of the types of service we offer (clean - move - repairs/maintenance) which are:
CLEAN - windows, gutters, solar panels, driveways/paths, carpets.
MOVE - Small/medium size house/office moves, large item pick-up & delivery, yard clean-up and removal.
General maintenance and repairs.

I would like the blue logo on a gray background.

Thanks

```html
<!DOCTYPE html>
<html lang="en">
<head>
<meta charset="utf-8">
<title>Brightway Haul &amp; Upkeep Services – Business Card</title>
<link href="https://fonts.googleapis.com/css2?family=PT+Sans:wght@400;700&display=swap" rel="stylesheet">
<style>
  :root {
    --page: #e6e4e2;
    --card-light: #f4f4f4;
    --card-mid: #c9c9c9;
    --card-dark: #a9a9a9;
    --brand-blue: #1f6fbf;
    --brand-blue-light: #7fb6e6;
    --ink: #1d1d1d;
    --band-black: #1a1a1a;
    --white: #ffffff;
  }
  * { box-sizing: border-box; margin: 0; padding: 0; }
  html, body { width: 1200px; height: 682px; overflow: hidden; }
  body {
    background: var(--page);
    font-family: "PT Sans", Arial, sans-serif;
    position: relative;
  }
  .card {
    position: absolute;
    top: 176px;
    width: 556px;
    height: 330px;
    overflow: hidden;
    box-shadow: 0 6px 18px rgba(0,0,0,0.22);
    background: linear-gradient(180deg, var(--card-dark) 0%, var(--card-mid) 40%, var(--card-light) 100%);
  }
  .card--front { left: 29px; }
  .card--back { left: 615px; }

  /* Front */
  .brand {
    position: absolute;
    left: 0; right: 0;
    display: flex;
    align-items: center;
    justify-content: center;
    gap: 14px;
  }
  .card--front .brand { top: 78px; }
  .brand__mark {
    width: 34px; height: 34px;
    background: var(--brand-blue);
    flex: none;
  }
  .brand__name {
    font-weight: 700;
    color: var(--brand-blue);
    font-size: 31px;
    line-height: 1.05;
    letter-spacing: 0.2px;
    text-transform: uppercase;
    max-width: 430px;
  }
  .band-web {
    position: absolute;
    left: 0; right: 0; top: 210px;
    height: 44px;
    background: var(--band-black);
    color: var(--white);
    display: flex; align-items: center; justify-content: center;
    font-weight: 700;
    font-size: 17px;
    letter-spacing: 4px;
  }
  .band-contact {
    position: absolute;
    left: 0; right: 0; top: 254px; bottom: 0;
    background: var(--brand-blue);
    color: var(--white);
    display: flex; align-items: center; justify-content: center;
    gap: 24px;
    font-size: 15px;
  }
  .contact { display: flex; align-items: center; gap: 6px; }
  .contact svg { width: 14px; height: 14px; flex: none; }

  /* Back */
  .card--back .brand { top: 34px; justify-content: flex-start; padding-left: 40px; }
  .card--back .brand__name { font-size: 24px; max-width: 460px; }
  .services {
    position: absolute;
    left: 40px; right: 32px; top: 128px;
    color: var(--ink);
  }
  .services__title {
    color: var(--brand-blue);
    font-size: 24px;
    font-weight: 400;
    letter-spacing: 2px;
    margin-bottom: 12px;
  }
  .service {
    display: grid;
    grid-template-columns: 66px 1fr;
    font-size: 15px;
    line-height: 1.3;
    margin-bottom: 8px;
  }
  .service__label { color: var(--brand-blue); font-weight: 700; font-size: 17px; }
  .services__general {
    color: var(--brand-blue);
    font-weight: 700;
    font-size: 18px;
    letter-spacing: 1.5px;
    margin-top: 6px;
  }
</style>
</head>
<body>

  <section class="card card--front" aria-label="Business card front">
    <div class="brand">
      <span class="brand__mark"></span>
      <span class="brand__name">Brightway Haul &amp; Upkeep Services</span>
    </div>
    <div class="band-web">www.brightwayhaul.com.au</div>
    <div class="band-contact">
      <span class="contact">
        <svg viewBox="0 0 24 24" fill="#ffffff" aria-hidden="true"><path d="M6.6 10.8a15.1 15.1 0 0 0 6.6 6.6l2.2-2.2c.3-.3.7-.4 1-.2 1.1.4 2.3.6 3.6.6.6 0 1 .4 1 1V20c0 .6-.4 1-1 1A17 17 0 0 1 3 4c0-.6.4-1 1-1h3.5c.6 0 1 .4 1 1 0 1.3.2 2.5.6 3.6.1.3 0 .7-.2 1z"/></svg>
        0487650392
      </span>
      <span class="contact">
        <svg viewBox="0 0 24 24" fill="#ffffff" aria-hidden="true"><path d="M2 5h20v14H2z M2 5l10 8 10-8" stroke="#1f6fbf" stroke-width="1.5"/></svg>
        brightwayhaulandupkeep@mailbox.example
      </span>
    </div>
  </section>

  <section class="card card--back" aria-label="Business card back">
    <div class="brand">
      <span class="brand__mark"></span>
      <span class="brand__name">Brightway Haul &amp; Upkeep Services</span>
    </div>
    <div class="services">
      <h2 class="services__title">Services we offer</h2>
      <div class="service">
        <span class="service__label">CLEAN:</span>
        <span>Windows, Gutters, Solar Panels, Driveways/paths, Carpets.</span>
      </div>
      <div class="service">
        <span class="service__label">MOVE:</span>
        <span>Small/medium Size House/office Moves, Large Item Pick-up &amp; Delivery, Yard Clean-up And Removal.</span>
      </div>
      <p class="services__general">General maintenance and repairs.</p>
    </div>
  </section>

</body>
</html>
```